Law Offices business card

Hi there, I'll need business card for the Law Offices of Colin Matheny. The information must convey his strategic approach and quick resolution to complex business litigation needs. Please emphasize Civil Litigation, Corporate Law, Business Governance and Real Estate Law. Colin has over 25 years of experience in these fields.The card should be modern and edgy and the message should be clear. Please consult his current website for ideas.

```html
<!DOCTYPE html>
<html lang="en">
<head>
<meta charset="utf-8">
<title>Law Offices of Colin Matheny – Business Card</title>
<link rel="stylesheet" href="https://fonts.googleapis.com/css2?family=Arimo:wght@400;700&family=Playfair+Display:wght@400;700&display=swap">
<style>
  :root {
    --stage: #3a3a3c;
    --card-black: #050505;
    --brand-red: #c9504f;
    --white: #ffffff;
    --soft-grey: #d4d4d4;
    --muted-grey: #bdbdbd;
  }
  * { box-sizing: border-box; margin: 0; padding: 0; }
  html, body { width: 1200px; height: 950px; overflow: hidden; }
  body {
    background: var(--stage);
    font-family: "Arimo", Arial, sans-serif;
    position: relative;
  }
  .card {
    position: absolute;
    width: 760px;
    height: 434px;
    background: var(--card-black);
    overflow: hidden;
    box-shadow: 0 14px 30px rgba(0,0,0,0.45);
  }
  .card--back { left: 90px; top: 48px; }
  .card--front { left: 350px; top: 468px; }

  /* Back side */
  .back-brand {
    position: absolute;
    left: 0; right: 0; top: 150px;
    display: flex; align-items: center; justify-content: center; gap: 14px;
  }
  .back-brand__square { width: 18px; height: 18px; background: var(--brand-red); }
  .back-brand__name {
    font-family: "Playfair Display", Georgia, serif;
    font-size: 40px; color: var(--white); letter-spacing: 1px;
  }
  .back-web {
    position: absolute;
    left: 0; right: 0; top: 252px;
    display: flex; align-items: center; justify-content: center; gap: 16px;
  }
  .back-web__rule { width: 70px; height: 2px; background: var(--brand-red); }
  .back-web__text { color: var(--soft-grey); font-size: 16px; letter-spacing: 4px; }

  /* Front side */
  .front-bg { position: absolute; inset: 0; }
  .holder {
    position: absolute; right: 40px; top: 34px; text-align: right; color: var(--white);
  }
  .holder__name { font-size: 24px; font-weight: 700; }
  .holder__title { font-size: 16px; margin-top: 4px; }
  .firm {
    position: absolute; left: 44px; top: 170px;
    font-family: "Playfair Display", Georgia, serif;
    color: var(--white); font-weight: 700;
  }
  .firm__lead { font-size: 14px; letter-spacing: 1.5px; text-transform: uppercase; }
  .firm__name { font-size: 40px; line-height: 1; margin-top: 6px; }
  .firm__suffix { font-size: 20px; }
  .contacts {
    position: absolute; left: 62px; top: 306px; list-style: none;
    color: var(--white); font-size: 15px;
  }
  .contacts li { display: flex; align-items: center; gap: 10px; height: 24px; }
  .contacts svg { width: 14px; height: 14px; fill: var(--brand-red); flex: none; }
  .address {
    position: absolute; right: 40px; top: 196px; text-align: right;
    font-style: normal;
    color: var(--soft-grey); font-size: 16px; line-height: 1.5;
  }
  .address__web { letter-spacing: 3px; color: var(--muted-grey); }
</style>
</head>
<body>

<section class="card card--back" aria-label="Business card, back side">
  <div class="back-brand">
    <span class="back-brand__square"></span>
    <span class="back-brand__name">Colin Matheny</span>
  </div>
  <div class="back-web">
    <span class="back-web__rule"></span>
    <span class="back-web__text">www.mathenylaw.com</span>
    <span class="back-web__rule"></span>
  </div>
</section>

<section class="card card--front" aria-label="Business card, front side">
  <svg class="front-bg" viewBox="0 0 760 434" width="760" height="434" aria-hidden="true">
    <path fill="var(--brand-red)" d="M0 0 H760 V150 C560 148 300 40 0 52 Z"/>
    <path fill="var(--white)" d="M0 52 C300 40 560 148 760 150 V160 C560 160 300 54 0 60 Z"/>
  </svg>

  <div class="holder">
    <div class="holder__name">Nora Ellison</div>
    <div class="holder__title">President</div>
  </div>

  <div class="firm">
    <div class="firm__lead">Law Offices of</div>
    <div class="firm__name">Colin<br>Matheny<span class="firm__suffix">, PA</span></div>
  </div>

  <ul class="contacts">
    <li>
      <svg viewBox="0 0 16 16"><path d="M3 1h3l1.5 4-2 1.3a9 9 0 0 0 4.2 4.2L11 8.5l4 1.5v3a2 2 0 0 1-2 2A12 12 0 0 1 1 3a2 2 0 0 1 2-2z"/></svg>
      <span>512 8470 2196</span>
    </li>
    <li>
      <svg viewBox="0 0 16 16"><path d="M4 0h8a1 1 0 0 1 1 1v14a1 1 0 0 1-1 1H4a1 1 0 0 1-1-1V1a1 1 0 0 1 1-1zm1 2v10h6V2zm3 11a1 1 0 1 0 0 2 1 1 0 0 0 0-2z"/></svg>
      <span>512 3758 6410</span>
    </li>
    <li>
      <svg viewBox="0 0 16 16"><path d="M4 0h8v5H4zM1 6h14v8h-3v2H4v-2H1zm4 5v4h6v-4z"/></svg>
      <span>512 4627 3385</span>
    </li>
    <li>
      <svg viewBox="0 0 16 16"><path d="M0 3h16v1.5L8 9 0 4.5zm0 3.2 8 4.5 8-4.5V13H0z"/></svg>
      <span>nora@mathenylaw.com</span>
    </li>
  </ul>

  <address class="address">
    2140 Harlow Ridge Road<br>
    Cedar Bluff, TX 78210<br>
    <span class="address__web">www.mathenylaw.com</span>
  </address>
</section>

</body>
</html>
```